Ward Compass Business Card Design*

We need a business card design for our company Ward Compass. Our company is specialized in providing online consulting services regarding medical institutions, hospitals and doctors. We work with patients worldwide looking to choose between healthcare providers. We have a website you may use as a reference, where we list doctors and clinics worldwide. So we target Medical providers as well as patients worldwide.
Target Market(s)
Medical Providers and patients around the world
Industry/Entity Type
Medical
Contact Information for Business Card
Salwa Kettani
CEO
+90 612 348 2175
info@wardcompass.example
www.wardcompass.example
14 Annakhil 7 H.R.B. Rabat, Morocco
Requirements
Must have
- Company logo/name on one full side, personal info and smaller logo and company name on the other side.
Nice to have
- Smart and elegant design

```html
<!DOCTYPE html>
<html lang="en">
<head>
<meta charset="utf-8">
<title>Ward Compass – Business Card</title>
<link rel="stylesheet" href="https://fonts.googleapis.com/css2?family=Montserrat:wght@300;400;700&family=Open+Sans:wght@400;600&display=swap">
<style>
  :root {
    --brand-blue: #1f4f96;
    --brand-blue-dark: #163d78;
    --swoosh-grey: #a3a5a8;
    --swoosh-light: #c9cacc;
    --card-white: #f7f7f8;
    --ring-grey: #e6e7e9;
    --ring-inner: #f2f2f3;
    --text-grey: #7b7d80;
    --stage: #e4e2de;
  }
  html, body {
    margin: 0;
    width: 1200px;
    height: 780px;
    overflow: hidden;
    background: var(--stage);
  }
  .canvas { position: relative; width: 1200px; height: 780px; }
  .card {
    position: absolute;
    width: 580px;
    height: 330px;
    border-radius: 16px;
    overflow: hidden;
    background: var(--card-white);
    box-shadow: 0 10px 28px rgba(0,0,0,.18);
  }
  .card svg.card-art { position: absolute; inset: 0; }
  .card-front { left: 60px; top: 45px; }
  .card-back { left: 560px; top: 405px; }

  .brand {
    position: absolute;
    display: flex;
    align-items: center;
    gap: 14px;
  }
  .brand-dot {
    width: 34px; height: 34px; border-radius: 50%;
    background: var(--brand-blue);
    flex: none;
  }
  .brand-name {
    font-family: "Montserrat", sans-serif;
    font-weight: 700;
    color: var(--brand-blue);
    letter-spacing: .5px;
    text-transform: uppercase;
    white-space: nowrap;
  }
  .card-front .brand { left: 38px; top: 158px; }
  .card-front .brand-name { font-size: 28px; }
  .card-back .brand { left: 0; right: 0; top: 142px; justify-content: center; }
  .card-back .brand-dot { width: 40px; height: 40px; }
  .card-back .brand-name { font-size: 32px; }

  .contact {
    position: absolute;
    right: 46px;
    top: 34px;
    text-align: right;
    font-family: "Open Sans", sans-serif;
  }
  .contact-name {
    font-family: "Montserrat", sans-serif;
    font-size: 17px;
    color: var(--brand-blue);
    letter-spacing: .5px;
    margin: 0;
  }
  .contact-name .given { font-weight: 700; }
  .contact-name .family { font-weight: 300; color: var(--text-grey); }
  .contact-role {
    font-size: 11px; color: var(--text-grey); margin: 2px 0 12px; letter-spacing: 1px;
  }
  .contact-list { list-style: none; margin: 0; padding: 0; }
  .contact-list li {
    display: flex; justify-content: flex-end; align-items: center; gap: 7px;
    font-size: 11.5px; color: var(--text-grey); line-height: 21px;
  }
  .contact-icon {
    width: 15px; height: 15px; border-radius: 50%;
    background: var(--brand-blue);
    display: inline-flex; align-items: center; justify-content: center;
  }
</style>
</head>
<body>
<div class="canvas">

  <!-- Personal side -->
  <section class="card card-front" aria-label="Business card, personal side">
    <svg class="card-art" width="580" height="330" viewBox="0 0 580 330" aria-hidden="true">
      <circle cx="470" cy="85" r="175" fill="var(--ring-grey)"/>
      <circle cx="470" cy="85" r="140" fill="var(--ring-inner)"/>
      <path d="M0,296 Q310,282 580,150 Q330,268 0,306 Z" fill="var(--swoosh-light)"/>
      <path d="M0,308 Q320,292 580,178 L580,196 Q330,296 0,316 Z" fill="var(--swoosh-grey)"/>
      <path d="M0,330 L0,320 Q330,304 580,206 L580,330 Z" fill="var(--brand-blue)"/>
    </svg>

    <div class="brand">
      <span class="brand-dot"></span>
      <span class="brand-name">Ward Compass</span>
    </div>

    <div class="contact">
      <p class="contact-name"><span class="given">SALWA</span> <span class="family">KETTANI</span></p>
      <p class="contact-role">CEO</p>
      <ul class="contact-list">
        <li>+90 612 348 2175
          <span class="contact-icon"><svg width="9" height="9" viewBox="0 0 10 10"><path d="M2 1 L4 1 L4.6 3.2 L3.4 4 Q4.3 5.9 6 6.6 L6.8 5.4 L9 6 L9 8 Q5 9 1 5 Q1.2 2.6 2 1 Z" fill="#fff"/></svg></span>
        </li>
        <li>info@wardcompass.example
          <span class="contact-icon"><svg width="9" height="9" viewBox="0 0 10 10"><rect x="1" y="2.5" width="8" height="5.5" fill="none" stroke="#fff" stroke-width="1"/><path d="M1 2.5 L5 5.5 L9 2.5" fill="none" stroke="#fff" stroke-width="1"/></svg></span>
        </li>
        <li>www.wardcompass.example
          <span class="contact-icon"><svg width="9" height="9" viewBox="0 0 10 10"><circle cx="5" cy="5" r="3.8" fill="none" stroke="#fff" stroke-width="1"/><ellipse cx="5" cy="5" rx="1.6" ry="3.8" fill="none" stroke="#fff" stroke-width=".8"/><path d="M1.2 5 H8.8" stroke="#fff" stroke-width=".8"/></svg></span>
        </li>
      </ul>
    </div>
  </section>

  <!-- Brand side -->
  <section class="card card-back" aria-label="Business card, brand side">
    <svg class="card-art" width="580" height="330" viewBox="0 0 580 330" aria-hidden="true">
      <path d="M0,0 H580 V30 Q300,50 0,108 Z" fill="var(--brand-blue)"/>
      <path d="M0,116 Q290,58 580,38 L580,46 Q300,70 0,128 Z" fill="var(--swoosh-grey)"/>
      <path d="M60,130 Q300,80 580,58 Q320,92 60,130 Z" fill="var(--swoosh-light)"/>
      <path d="M0,268 Q300,262 580,192 Q300,250 0,256 Z" fill="var(--swoosh-light)"/>
      <path d="M0,282 Q310,276 580,212 L580,224 Q320,288 0,292 Z" fill="var(--swoosh-grey)"/>
      <path d="M0,330 V300 Q320,296 580,232 V330 Z" fill="var(--brand-blue-dark)"/>
    </svg>

    <div class="brand">
      <span class="brand-dot"></span>
      <span class="brand-name">Ward Compass</span>
    </div>
  </section>

</div>
</body>
</html>
```